Personal training and nutrition business needs business card design

We need a business card that outlays our services and invites potential customers to join our team and take the first step to a healthier and more enjoyable life. We cater for any level of fitness and specialize in weight loss and conditioning, strength training, muscle gain and strength endurance. Whether you are just starting off or need some help getting to the next level of your journey we are here to get the job done.
We specialize in one on one or one on two personal training sessions and each program will be custom made to suit individual fitness goals of our clients

```html
<!DOCTYPE html>
<html lang="en">
<head>
<meta charset="utf-8">
<title>Pulse &amp; Motion – Business Card</title>
<link href="https://fonts.googleapis.com/css2?family=Exo+2:ital,wght@1,800&family=Roboto:wght@400;500;700&display=swap" rel="stylesheet">
<style>
  :root {
    --backdrop: #2b2b2d;
    --purple-deep: #5a3a8c;
    --purple-mid: #7c4a9e;
    --purple-light: #a05aa8;
    --paper: #f2f2f3;
    --paper-shade: #e2e2e4;
    --ink: #1a1a1a;
    --ink-soft: #333;
    --white: #f4f2f6;
  }
  * { margin: 0; padding: 0; box-sizing: border-box; }
  html, body { width: 1200px; height: 1138px; overflow: hidden; }
  body { background: var(--backdrop); position: relative; font-family: "Roboto", sans-serif; }

  .card {
    position: absolute; left: 275px; width: 622px; height: 376px;
    border-radius: 16px; overflow: hidden;
  }
  .card--front {
    top: 186px;
    background: linear-gradient(120deg, var(--purple-deep) 0%, var(--purple-mid) 55%, var(--purple-light) 100%);
    display: flex; flex-direction: column; align-items: center; justify-content: center;
  }
  .front__brand {
    font-family: "Roboto", sans-serif; font-weight: 700; font-size: 46px;
    letter-spacing: 2px; color: var(--white); text-transform: uppercase; line-height: 1;
    margin-top: -8px;
  }
  .front__services {
    margin-top: 16px; font-family: "Roboto", sans-serif; font-weight: 500; font-size: 16px;
    letter-spacing: 2.4px; color: var(--white); opacity: .9; text-transform: uppercase; word-spacing: 4px;
  }

  .card--back {
    top: 608px;
    background: linear-gradient(180deg, var(--paper) 0%, var(--paper) 55%, var(--paper-shade) 100%);
  }
  .back__brand {
    position: absolute; left: 80px; top: 95px; width: 190px;
    display: flex; flex-direction: column; align-items: center;
  }
  .brand__square {
    width: 62px; height: 62px; border-radius: 6px;
    background: linear-gradient(135deg, var(--purple-deep), var(--purple-light));
  }
  .brand__name {
    margin-top: 16px; font-family: "Roboto", sans-serif; font-weight: 700; font-size: 30px;
    line-height: 1; color: var(--ink); text-transform: uppercase; text-align: center; letter-spacing: 1px;
  }
  .brand__tagline {
    margin-top: 8px; font-size: 8.5px; font-weight: 500; letter-spacing: .6px;
    color: var(--purple-mid); text-transform: uppercase; white-space: nowrap;
  }

  .back__details { position: absolute; left: 341px; top: 84px; color: var(--ink-soft); font-size: 16px; }
  .person__name {
    font-family: "Exo 2", sans-serif; font-style: italic; font-weight: 800; font-size: 25px;
    letter-spacing: 1px; text-transform: uppercase; line-height: 1;
    background: linear-gradient(90deg, var(--purple-deep), var(--purple-light));
    -webkit-background-clip: text; background-clip: text; color: transparent;
  }
  .person__role { margin-top: 8px; }
  .contact { list-style: none; margin-top: 30px; }
  .contact__item { display: flex; align-items: center; height: 24px; }
  .contact__item svg { width: 14px; height: 14px; margin-right: 18px; fill: var(--purple-mid); }
  .contact__accent { color: var(--purple-mid); }
  .address { margin-top: 14px; font-style: normal; line-height: 24px; }
</style>
</head>
<body>
  <section class="card card--front" aria-label="Card front">
    <h1 class="front__brand">Pulse &amp; Motion</h1>
    <p class="front__services">Personal Training &nbsp;|&nbsp; Nutrition &nbsp;|&nbsp; Motivation</p>
  </section>

  <section class="card card--back" aria-label="Card back">
    <div class="back__brand">
      <div class="brand__square"></div>
      <p class="brand__name">Pulse &amp;<br>Motion</p>
      <p class="brand__tagline">Personal training. Nutrition. Motivation</p>
    </div>

    <div class="back__details">
      <h2 class="person__name">Sam Rivera</h2>
      <p class="person__role">Personal Trainer</p>
      <ul class="contact">
        <li class="contact__item">
          <svg viewBox="0 0 16 16" aria-hidden="true"><path d="M2 6c0-2 2.5-3 6-3s6 1 6 3v1h-3V5.5H5V7H2z"/><rect x="3" y="8" width="10" height="6" rx="1"/></svg>
          +12 (555) 014-2290
        </li>
        <li class="contact__item">
          <svg viewBox="0 0 16 16" aria-hidden="true"><path d="M1 3h14v10H1z M2.5 4.5 8 9l5.5-4.5" stroke="#f2f2f3" stroke-width="1.2"/></svg>
          sam@pulsemotion.com
        </li>
        <li class="contact__item">
          <svg viewBox="0 0 16 16" aria-hidden="true"><circle cx="8" cy="8" r="7"/><path d="M1 8h14M8 1c-3 3-3 11 0 14M8 1c3 3 3 11 0 14" stroke="#f2f2f3" stroke-width="1" fill="none"/></svg>
          <span>www.<span class="contact__accent">pulsemotion</span>.com</span>
        </li>
      </ul>
      <address class="address">1420 Cedar Ridge Lane<br>Ridgeview Texas 75001</address>
    </div>
  </section>
</body>
</html>
```